Marla’s Sandwich Corner Grand Opening Door Flyer

1. Project Title
• “Flyer Design for Sandwich Shop Grand Opening”
• Why it’s effective: Direct and to the point, highlighting the purpose of the design.

2. Project Description
• “We’re looking for a professional designer to create a vibrant and modern flyer for our sandwich shop, Marla’s Corner. The flyer should emphasize our handcrafted sandwiches, fresh-baked bread, and house-made meats. As a women & family-owned business, we want this aspect prominently displayed. The flyer should also include our logo, a ‘Grand Opening’ and our website: MarlasCorner.example. We want the design to be clean, bold, and visually appealing to attract customers. We also would like a QR code so they can scan to load of the website to order online, but also list it.
• Why it’s effective: Clear goals, modern style preference, and necessary details outlined.

3. Visual Style
• “Modern, bold, and clean design with bright, appetizing colors. Focus on high-quality imagery of sandwiches, sleek fonts, and an inviting layout.”
• Why it’s effective: Communicates the desired aesthetic and tone.

4. Key Details to Include
• Business Name: Marla’s Sandwich Corner
• Taglines:
“Women & Family Owned”
“Handcrafted Sandwiches Made with Love”
“Fresh Baked Bread”
“House-made Slow Roasted House Specialties”
“Gluten-Friendly”
“Vegan-Friendly”
“7:00am Fresh Daily Grounded Coffee and Breakfast”

• Call-to-Action: “Order Online at MarlasCorner.example”
• Placeholder for the logo.
• Size: 4.25 x 11 (Door Hanger)
• File Format: High-resolution PDF, JPEG, or PNG.
• Print-Ready: Include bleed margins and ensure print clarity.

6. Tone
• Friendly and professional. Highlighting that your business is women-owned adds a unique and personal touch vs deli meat shops. We are a gourmet sandwich shop, with fresh baked bread, house-made meats, with gluten and vegan options. Each sandwich is made with love.

Target Market(s)

Coffee drinkers for morning crowd and sandwiches for lunch

Industry/Entity Type

Sandwich Shop

Colors
EB3D1F
EC4F4E
F09395
F8D3D4
FCEDEE

Requirements
Must have
• See Description
Nice to have
• Use website to get a feel for color theme
Should not have
• NA

```html
<!DOCTYPE html>
<html lang="en">
<head>
<meta charset="utf-8">
<title>Marla’s Sandwich Corner – Grand Opening Door Hanger</title>
<link rel="stylesheet" href="https://fonts.googleapis.com/css2?family=Lora:ital,wght@1,700&family=DM+Serif+Display:ital@0;1&family=Montserrat:wght@500;800&family=Oleo+Script&family=Lobster&display=swap">
<style>
  :root{
    --orange:#eb3d1f;
    --pink-light:#f8d3d4;
    --black:#151515;
    --white:#ffffff;
    --backdrop:#6b6b6b;
    --slot:#666666;
    --photo-dark:#3c3c3c;
    --photo-light:#d9d9d9;
    --emblem:#fff200;
  }
  *{margin:0;padding:0;box-sizing:border-box}
  html,body{width:900px;height:1200px;overflow:hidden;background:var(--backdrop)}
  .canvas{position:relative;width:900px;height:1200px;background:var(--backdrop)}
  .hanger{position:absolute;left:258px;top:103px;width:384px;height:992px;background:var(--white);overflow:hidden}
  .hanger-shapes{position:absolute;inset:0}
  .brand-name{position:absolute;top:34px;left:0;width:100%;text-align:center;
    font-family:"Montserrat",sans-serif;font-weight:800;font-size:20px;color:var(--orange);letter-spacing:.3px}
  .headline-grand{position:absolute;left:128px;top:186px;font-family:"Lora",serif;font-style:italic;font-weight:700;
    font-size:64px;line-height:1;color:var(--orange)}
  .headline-opening{position:absolute;right:40px;top:256px;font-family:"Oleo Script",cursive;font-style:italic;
    font-size:31px;line-height:1;color:var(--black);transform:skewX(-8deg)}
  .coffee-badge{position:absolute;left:243px;top:306px;width:124px;height:124px;border-radius:50%;
    background:var(--orange);color:var(--white);text-align:center;padding-top:25px}
  .coffee-badge .time{font-family:"Montserrat",sans-serif;font-weight:800;font-size:19px;line-height:1}
  .coffee-badge .small{font-family:"Lobster",cursive;font-size:11px;line-height:1.2;display:block}
  .coffee-badge .big{font-family:"Lobster",cursive;font-size:21px;line-height:1.05;display:block}
  .owned-stack{position:absolute;left:20px;top:684px;width:150px;text-align:center;color:var(--white);
    font-family:"DM Serif Display",serif;line-height:1.04}
  .owned-stack .women{font-style:italic;font-size:36px}
  .owned-stack .and{font-size:35px}
  .owned-stack .bold{font-size:40px}
  .features{position:absolute;left:176px;top:656px;list-style:none}
  .feature{display:flex;align-items:center;height:63px}
  .feature-icon{width:36px;height:36px;flex:none}
  .feature-text{margin-left:16px;font-family:"Montserrat",sans-serif;font-weight:500;font-size:10px;
    line-height:1.35;color:var(--white);max-width:160px}
  .emblem{position:absolute;left:45px;top:845px;width:94px;height:94px;border-radius:50%;
    background:var(--emblem);border:1px solid #333}
  .cta{position:absolute;left:70px;top:932px;width:254px;text-align:center}
  .cta-lead{font-family:"Montserrat",sans-serif;font-weight:500;font-style:italic;font-size:15px;color:var(--black);line-height:1.1}
  .cta-url{font-family:"Lora",serif;font-style:italic;font-weight:700;font-size:21px;color:var(--orange);line-height:1.2}
</style>
</head>
<body>
<div class="canvas">
  <div class="hanger">
    <svg class="hanger-shapes" width="384" height="992" viewBox="0 0 384 992" aria-hidden="true">
      <defs>
        <linearGradient id="sky" x1="0" y1="0" x2="0" y2="1">
          <stop offset="0" stop-color="#ffffff"/>
          <stop offset="1" stop-color="#ececec"/>
        </linearGradient>
        <linearGradient id="storefront" x1="0" y1="0" x2="0" y2="1">
          <stop offset="0" stop-color="var(--photo-light)"/>
          <stop offset=".45" stop-color="#9a9a9a"/>
          <stop offset=".55" stop-color="var(--photo-dark)"/>
          <stop offset="1" stop-color="#5a5a5a"/>
        </linearGradient>
      </defs>
      <rect x="0" y="180" width="384" height="260" fill="url(#sky)"/>
      <path d="M0 107 H240 A35 35 0 0 1 240 177 H0 Z" fill="var(--slot)"/>
      <path d="M0 268 C130 250 300 270 362 340 C395 420 370 560 262 612 C170 640 60 632 0 618 Z" fill="var(--white)"/>
      <path d="M0 282 C120 266 285 284 344 345 C375 420 356 545 258 596 C170 624 60 618 0 604 Z"
            fill="url(#storefront)" role="img" aria-label="Photo of the shop front with the team celebrating"/>
      <path d="M0 262 C110 240 220 250 280 300" fill="none" stroke="var(--orange)" stroke-width="9" stroke-linecap="round"/>
      <path d="M0 620 C120 645 250 640 384 600 V992 H0 Z" fill="var(--orange)"/>
      <path d="M190 632 C300 628 350 612 384 596 V992 H210 C200 880 180 760 190 632 Z" fill="var(--black)"/>
      <path d="M0 948 C120 918 270 896 384 905 V992 H0 Z" fill="var(--orange)"/>
      <path d="M0 958 C120 930 270 912 384 922 V992 H0 Z" fill="var(--white)"/>
    </svg>

    <div class="brand-name">Marla’s Sandwich Corner</div>

    <div class="headline-grand">Grand</div>
    <div class="headline-opening">Opening</div>

    <div class="coffee-badge">
      <div class="time">7:00am</div>
      <span class="small">Fresh Daily Grounded</span>
      <span class="big">Coffee</span>
      <span class="small">and Breakfast</span>
    </div>

    <div class="owned-stack">
      <div class="women">women</div>
      <div class="and">and</div>
      <div class="bold">family</div>
      <div class="bold">owned</div>
    </div>

    <ul class="features">
      <li class="feature">
        <svg class="feature-icon" viewBox="0 0 34 34" aria-hidden="true">
          <circle cx="17" cy="17" r="15.5" fill="var(--black)" stroke="var(--orange)" stroke-width="2.5"/>
          <path d="M9 15 H25 V23 Q25 25 23 25 H11 Q9 25 9 23 Z M7 15 H27 M14 12 Q17 9 20 12" fill="none" stroke="var(--orange)" stroke-width="2"/>
        </svg>
        <span class="feature-text">House-made Slow Roasted House Specialties</span>
      </li>
      <li class="feature">
        <svg class="feature-icon" viewBox="0 0 34 34" aria-hidden="true">
          <circle cx="17" cy="17" r="15.5" fill="var(--black)" stroke="var(--orange)" stroke-width="2.5"/>
          <path d="M8 22 Q8 16 17 16 Q26 16 26 22 Z" fill="var(--orange)"/>
          <path d="M13 13 Q12 11 13 9 M17 13 Q16 11 17 9 M21 13 Q20 11 21 9" fill="none" stroke="var(--orange)" stroke-width="1.6"/>
        </svg>
        <span class="feature-text">Fresh Baked Breadrafted Sandwiches Made with Love</span>
      </li>
      <li class="feature">
        <svg class="feature-icon" viewBox="0 0 34 34" aria-hidden="true">
          <circle cx="17" cy="17" r="15.5" fill="var(--black)" stroke="var(--orange)" stroke-width="2.5"/>
          <path d="M10 24 Q10 11 24 10 Q24 24 10 24 Z" fill="var(--orange)"/>
          <path d="M10 24 L20 14" stroke="var(--black)" stroke-width="1.5"/>
        </svg>
        <span class="feature-text">Vegan-Friendly</span>
      </li>
      <li class="feature">
        <svg class="feature-icon" viewBox="0 0 34 34" aria-hidden="true">
          <circle cx="17" cy="17" r="15.5" fill="var(--black)" stroke="var(--orange)" stroke-width="2.5"/>
          <path d="M17 9 V26 M17 14 L13 11 M17 14 L21 11 M17 19 L13 16 M17 19 L21 16 M17 24 L13 21 M17 24 L21 21" fill="none" stroke="var(--orange)" stroke-width="2"/>
          <path d="M9 25 L25 9" stroke="var(--orange)" stroke-width="2"/>
        </svg>
        <span class="feature-text">Gluten-Friendly</span>
      </li>
    </ul>

    <div class="emblem" role="img" aria-label="Shop emblem area"></div>

    <div class="cta">
      <div class="cta-lead">Order Online at</div>
      <div class="cta-url">MarlasCorner.example</div>
    </div>
  </div>
</div>
</body>
</html>
```